Bright Harbor, LLC Business Card Design

We need a product business card designed for a new company Bright Harbor, LLC. We make and resell waterless RV cleaner, polish and protectant. It cleans and protects in a simple spray and wipe step leaving the surface protected and conditioned to repel dust, dirt, water, smudges, bugs and fingerprints while preventing fogging. Safe on acrylic, plexiglas, lexan, plastic, rubber, painted surfaces, chrome, stainless, aluminum, vinyl, leather, glass.... This is an eco-friendly green product.

We want to play off the company name to tell the consumer that the product is easy to use and associate to the nostalgics 1950's in the USA... Thinking old travel trailer with hot rod truck pulling it as the graphic, maybe the husband cleaning the truck and the wife cleaning the trailer for a Bright Harbor surface.
Updates

Just posted our newly finished logo. Need to have "Cleaner and Protectant" added to the design as well. Thanks everyone that has submitted thus far, i am working to get comments on all.

If you need a different file format, please let me know. Thank you.

Most important info, is the logo, website and the words "Cleaner" or "Clean" along "Protectant" or "Protect" the remainder is of less importance. Highlight: www.brightharborwash.example Focus is on company brand for Brighter Harbor Cleaner product: However, need a section for the following contact info: Walt Ferris (xxx) xxx-xxxx email address Would like space for QR Code if possible.

Target Market(s)

Adults in the USA between ages of 35-75 that are actively involved in the Recreational Vehicle (RV), travel trailer, and hot rod lifestyle. We are targeting the RV marked of the high end travel, 5th wheel and bus RV market. Along with hot rods, automotive and motorcycle market.

Industry/Entity Type

Travel

Requirements
Must have
• Most important info, is the logo, website and the words "Cleaner" or "Clean" along "Protectant" or "Protect" the remainder is of less importance.

Highlight:
www.brightharborwash.example

Focus is on company brand for Brighter Harbor Cleaner product: However, need a section for the following contact info:

Walt Ferris
(xxx) xxx-xxxx
email address
Nice to have
• Would like a space for a QR Code.

```html
<!DOCTYPE html>
<html lang="en">
<head>
<meta charset="utf-8">
<title>Bright Harbor, LLC – Business Card</title>
<link rel="stylesheet" href="https://fonts.googleapis.com/css2?family=Saira+Condensed:wght@700&family=Saira:wght@400;500&display=swap">
<style>
  :root {
    --backdrop: #6a6a6a;
    --card-white: #ffffff;
    --card-shade: #e9e9e9;
    --ink: #1d1d1f;
    --ink-soft: #3a3a3c;
    --blue-light: #1e95dc;
    --blue-deep: #3645a8;
    --swoosh-light: #9a9a9a;
    --swoosh-dark: #2b2b2b;
    --on-blue: #ffffff;
  }
  * { box-sizing: border-box; margin: 0; padding: 0; }
  html, body { width: 1200px; height: 750px; overflow: hidden; }
  body {
    background: var(--backdrop);
    display: flex;
    align-items: center;
    justify-content: center;
    gap: 40px;
    font-family: "Saira", sans-serif;
  }
  .card {
    position: relative;
    width: 540px;
    height: 309px;
    background: linear-gradient(160deg, var(--card-white) 40%, var(--card-shade));
    box-shadow: 0 14px 30px rgba(0,0,0,.35);
    overflow: hidden;
  }
  .brand-name {
    font-family: "Saira Condensed", sans-serif;
    font-weight: 700;
    color: var(--ink);
    text-transform: uppercase;
    letter-spacing: .5px;
    line-height: 1;
  }
  .tagline {
    font-family: "Saira", sans-serif;
    font-weight: 500;
    color: var(--blue-deep);
    text-transform: uppercase;
    letter-spacing: 3px;
    line-height: 1;
  }
  .card--front {
    display: flex; flex-direction: column;
    align-items: center; justify-content: center; gap: 12px;
  }
  .card--front .brand-name { font-size: 54px; }
  .card--front .tagline { font-size: 15px; }

  .card__art { position: absolute; inset: 0; width: 100%; height: 100%; }
  .brand-block { position: absolute; left: 36px; top: 88px; }
  .card--back .brand-name { font-size: 36px; }
  .card--back .tagline { font-size: 10px; letter-spacing: 2px; margin-top: 7px; }
  .holder { position: absolute; left: 36px; top: 196px; color: var(--ink); }
  .holder__name { font-size: 16px; font-weight: 500; letter-spacing: 2px; text-transform: uppercase; }
  .holder__title { font-size: 11px; color: var(--ink-soft); margin-top: 1px; }

  .contact {
    position: absolute; right: 20px; top: 22px;
    list-style: none; text-align: right; color: var(--on-blue);
    font-size: 11px; line-height: 1.35;
  }
  .contact__address { margin-bottom: 12px; }
  .contact li { display: flex; justify-content: flex-end; align-items: center; gap: 6px; margin-bottom: 5px; }
  .contact svg { width: 11px; height: 11px; flex: none; }

  .qr-space {
    position: absolute; right: 20px; bottom: 18px;
    width: 72px; height: 72px;
    background: var(--card-white);
    border-radius: 3px;
  }
</style>
</head>
<body>
  <section class="card card--front" aria-label="Card front">
    <h1 class="brand-name">Bright Harbor</h1>
    <p class="tagline">Cleaner and Protectant</p>
  </section>

  <section class="card card--back" aria-label="Card back">
    <svg class="card__art" viewBox="0 0 540 309" aria-hidden="true">
      <defs>
        <linearGradient id="blueFill" x1="1" y1="0" x2="0" y2="1">
          <stop offset="0" stop-color="var(--blue-light)"/>
          <stop offset="1" stop-color="var(--blue-deep)"/>
        </linearGradient>
        <linearGradient id="swooshFill" x1="0" y1="0" x2="1" y2="0">
          <stop offset="0" stop-color="var(--swoosh-light)"/>
          <stop offset="1" stop-color="var(--swoosh-dark)"/>
        </linearGradient>
      </defs>
      <path d="M372 0 Q236 120 222 309 L262 309 Q278 120 402 0 Z" fill="url(#swooshFill)"/>
      <path d="M404 0 Q282 120 266 309 L540 309 L540 0 Z" fill="var(--card-white)"/>
      <path d="M410 0 Q290 120 272 309 L540 309 L540 0 Z" fill="url(#blueFill)"/>
    </svg>

    <div class="brand-block">
      <h2 class="brand-name">Bright Harbor</h2>
      <p class="tagline">Cleaner and Protectant</p>
    </div>
    <div class="holder">
      <p class="holder__name">Walt Ferris</p>
      <p class="holder__title">Managing Director</p>
    </div>

    <ul class="contact">
      <li class="contact__address">214 Dockside Lane, Suite 3<br>Harbor Point</li>
      <li>555 014 2280
        <svg viewBox="0 0 12 12"><path d="M2 1l2 0 1 3-1.5 1a6 6 0 0 0 3.5 3.5L8 7l3 1v2a1 1 0 0 1-1 1A9 9 0 0 1 1 2a1 1 0 0 1 1-1z" fill="currentColor"/></svg></li>
      <li>555 014 2281
        <svg viewBox="0 0 12 12"><rect x="3" y="0.5" width="6" height="11" rx="1" fill="none" stroke="currentColor"/><circle cx="6" cy="9.5" r=".7" fill="currentColor"/></svg></li>
      <li>555 014 2282
        <svg viewBox="0 0 12 12"><rect x="1" y="4" width="10" height="6" fill="currentColor"/><rect x="3" y="1" width="6" height="3" fill="none" stroke="currentColor"/></svg></li>
      <li>walt@brightharbor.example
        <svg viewBox="0 0 12 12"><rect x="1" y="2.5" width="10" height="7" fill="currentColor"/><path d="M1 2.5l5 4 5-4" fill="none" stroke="var(--blue-light)"/></svg></li>
      <li>www.brightharborwash.example
        <svg viewBox="0 0 12 12"><circle cx="6" cy="6" r="5" fill="none" stroke="currentColor"/><path d="M1 6h10M6 1c-2.5 3-2.5 7 0 10M6 1c2.5 3 2.5 7 0 10" fill="none" stroke="currentColor" stroke-width=".8"/></svg></li>
    </ul>

    <div class="qr-space" role="img" aria-label="Reserved space for QR code"></div>
  </section>
</body>
</html>
```